Modern Business Card

Modern professional business card with more than just logo and demographic info. Something memorable.

We are a trendy/modern chiropractic group with an emphasis on neurology, hence the minimalist-type brain logo. We want to convey that modern and technical aspect with professionalism and the elite nature of our practice environment.

```html
<!DOCTYPE html>
<html lang="en">
<head>
<meta charset="utf-8">
<title>Meridian Spine – Business Card</title>
<link href="https://fonts.googleapis.com/css2?family=Cinzel:wght@500&family=Tinos&display=swap" rel="stylesheet">
<style>
  :root {
    --brand-blue: #4a7fc1;
    --ink: #1c1c1c;
    --muted: #4a4a4a;
    --card: #ffffff;
    --backdrop: #e9e7e3;
  }
  html, body {
    margin: 0;
    padding: 0;
    width: 1200px;
    height: 800px;
    overflow: hidden;
    background: var(--backdrop);
  }
  .stage {
    position: relative;
    width: 1200px;
    height: 800px;
  }
  .card {
    position: absolute;
    top: 260px;
    width: 490px;
    height: 280px;
    background: var(--card);
    box-shadow: 0 2px 6px rgba(0,0,0,0.18);
    overflow: hidden;
  }
  .card--front { left: 99px; }
  .card--back { left: 614px; }

  .accent-block {
    position: absolute;
    top: 85px;
    width: 110px;
    height: 110px;
    background: var(--brand-blue);
  }
  .card--front .accent-block { left: 364px; }
  .card--back .accent-block { left: 10px; }

  .holder {
    position: absolute;
    left: 27px;
    top: 58px;
  }
  .holder__name {
    font-family: "Cinzel", serif;
    font-weight: 500;
    font-size: 17px;
    color: var(--brand-blue);
    letter-spacing: 0.5px;
    margin: 0;
    line-height: 1;
  }
  .holder__title {
    font-family: "Cinzel", serif;
    font-weight: 500;
    font-size: 11px;
    color: var(--ink);
    letter-spacing: 0.8px;
    margin: 4px 0 0;
  }
  .address {
    position: absolute;
    left: 27px;
    top: 112px;
    font-family: "Tinos", serif;
    font-size: 11.5px;
    line-height: 14px;
    color: var(--muted);
    margin: 0;
    font-style: normal;
  }
  .contacts {
    position: absolute;
    left: 27px;
    top: 153px;
    margin: 0;
    padding: 0;
    list-style: none;
    font-family: "Tinos", serif;
    font-size: 11.5px;
    color: var(--muted);
  }
  .contacts li {
    display: flex;
    align-items: center;
    height: 14.5px;
  }
  .contacts li.gap { margin-top: 1.5px; }
  .contacts svg {
    width: 9px;
    height: 9px;
    margin-right: 6px;
    fill: var(--brand-blue);
    flex: none;
  }

  .wordmark {
    position: absolute;
    left: 196px;
    top: 110px;
    display: flex;
    align-items: center;
  }
  .wordmark__square {
    width: 44px;
    height: 44px;
    background: var(--brand-blue);
    margin-right: 12px;
  }
  .wordmark__name {
    font-family: "Tinos", serif;
    font-size: 28px;
    line-height: 28px;
    color: var(--ink);
    letter-spacing: 0.5px;
    margin: 0;
  }
</style>
</head>
<body>
<main class="stage">
  <section class="card card--front" aria-label="Card front">
    <div class="holder">
      <p class="holder__name">Daniel Hartley</p>
      <p class="holder__title">President</p>
    </div>
    <address class="address">4120 Alder Court<br>Juneau, Alaska 99801</address>
    <ul class="contacts">
      <li>
        <svg viewBox="0 0 10 10" aria-hidden="true"><path d="M2 0.5 L3.6 2.6 L2.8 3.6 Q3.8 5.8 6.2 7.1 L7.3 6.3 L9.5 7.9 L8.4 9.5 Q4.5 9.3 1.6 5.8 Q0.3 3.6 0.6 1.6 Z"/></svg>
        555-214-0187
      </li>
      <li>
        <svg viewBox="0 0 10 10" aria-hidden="true"><path d="M2.5 0 H7.5 V10 H2.5 Z M3.3 1 V8 H6.7 V1 Z"/></svg>
        555-730-4462
      </li>
      <li>
        <svg viewBox="0 0 10 10" aria-hidden="true"><path d="M2.5 0.5 H7.5 V3.5 H2.5 Z M0.5 4 H9.5 V8 H0.5 Z M2.5 7 H7.5 V9.5 H2.5 Z"/></svg>
        555-389-2210
      </li>
      <li class="gap">
        <svg viewBox="0 0 10 10" aria-hidden="true"><path d="M0.5 2 H9.5 V8 H0.5 Z M1.3 2.6 L5 5.4 L8.7 2.6 V3.4 L5 6.2 L1.3 3.4 Z" fill-rule="evenodd"/></svg>
        name@meridianspine.com
      </li>
      <li class="gap">
        <svg viewBox="0 0 10 10" aria-hidden="true"><circle cx="5" cy="5" r="4.5"/></svg>
        www.meridianspine.com
      </li>
    </ul>
    <div class="accent-block" aria-hidden="true"></div>
  </section>

  <section class="card card--back" aria-label="Card back">
    <div class="accent-block" aria-hidden="true"></div>
    <div class="wordmark">
      <span class="wordmark__square" aria-hidden="true"></span>
      <p class="wordmark__name">MERIDIAN<br>SPINE</p>
    </div>
  </section>
</main>
</body>
</html>
```